Tech business card design

We need an amazing business card design for our new business 'Pexla' a marketing tech startup based in Sydney, Australia. We provide an online marketplace for businesses to search and buy advertising media, connect with service providers and learn more about marketing. We wish to communicate 'cool tech', reliability and professionalism and design based around our logo.

Target Market(s)

Business Owners

Contact Information for Business Card

Name
Position
Email Address
Website
Phone Number

Font styles to use
Other font styles liked:
• Avenir & Avenir Next

Colors

Designer to choose colors to be used in the design.

```html
<!DOCTYPE html>
<html lang="en">
<head>
<meta charset="utf-8">
<title>Pexla Business Card</title>
<link rel="stylesheet" href="https://fonts.googleapis.com/css2?family=Nunito+Sans:wght@400;700;900&display=swap">
<style>
  :root {
    --navy: #1f1d52;
    --navy-deep: #17163f;
    --navy-light: #2c2a6b;
    --paper: #ffffff;
    --ink: #111111;
    --muted: #555555;
    --pattern-grey: #e9e9ee;
    --backdrop: #2e3033;
  }
  * { box-sizing: border-box; margin: 0; padding: 0; }
  html, body { width: 1200px; height: 900px; overflow: hidden; }
  body {
    background: var(--backdrop);
    font-family: "Nunito Sans", "Avenir Next", Avenir, sans-serif;
    display: flex;
    flex-direction: column;
    align-items: center;
    justify-content: center;
    gap: 46px;
  }
  .card {
    position: relative;
    width: 660px;
    height: 377px;
    border-radius: 26px;
    overflow: hidden;
  }

  /* Front: contact side */
  .card-front { background: var(--paper); }
  .front-pattern {
    position: absolute;
    inset: 20px 30px 20px 30px;
    border-radius: 18px;
    background: radial-gradient(ellipse at 55% 50%, var(--pattern-grey) 0%, rgba(233,233,238,0.35) 60%, rgba(255,255,255,0) 85%);
  }
  .brand-block {
    position: absolute;
    left: 44px;
    top: 112px;
  }
  .wordmark {
    font-weight: 900;
    letter-spacing: -2px;
    line-height: 1;
  }
  .card-front .wordmark { font-size: 104px; color: var(--navy); }
  .tm {
    position: absolute;
    right: 2px;
    bottom: -16px;
    font-size: 10px;
    font-weight: 700;
  }
  .card-front .tm { color: var(--navy); }
  .divider {
    position: absolute;
    left: 322px;
    top: 70px;
    width: 40px;
    height: 240px;
  }
  .contact {
    position: absolute;
    left: 372px;
    top: 100px;
  }
  .person-name {
    font-size: 27px;
    font-weight: 900;
    color: var(--ink);
    letter-spacing: 0.5px;
    line-height: 1;
  }
  .person-role {
    font-size: 13px;
    color: var(--muted);
    margin-top: 3px;
  }
  .contact-list { list-style: none; margin-top: 16px; }
  .contact-list li {
    display: flex;
    align-items: center;
    gap: 12px;
    font-size: 17px;
    color: var(--ink);
    margin-bottom: 12px;
  }
  .contact-icon { width: 28px; height: 28px; flex: none; }

  /* Back: brand side */
  .card-back { background: var(--navy); }
  .back-map {
    position: absolute;
    left: 130px;
    top: 22px;
    width: 470px;
    height: 230px;
    border-radius: 40px;
    background: radial-gradient(ellipse at 55% 45%, rgba(255,255,255,0.32) 0%, rgba(255,255,255,0.12) 55%, rgba(31,29,82,0) 80%);
  }
  .back-brand {
    position: absolute;
    left: 200px;
    top: 222px;
  }
  .card-back .wordmark { font-size: 118px; color: var(--paper); }
  .card-back .tm { color: var(--paper); bottom: -14px; right: -12px; }
</style>
</head>
<body>

  <section class="card card-front">
    <div class="front-pattern" role="img" aria-label="Faint grey network-style world map pattern"></div>

    <div class="brand-block">
      <div class="wordmark">Pexla</div>
      <span class="tm">TM</span>
    </div>

    <svg class="divider" viewBox="0 0 40 240" aria-hidden="true">
      <polygon points="38,0 40,0 2,240 0,240" fill="var(--navy)"/>
    </svg>

    <div class="contact">
      <div class="person-name">MARA QUINLAN</div>
      <div class="person-role">Founder, Director</div>
      <ul class="contact-list">
        <li>
          <svg class="contact-icon" viewBox="0 0 28 28" aria-hidden="true">
            <circle cx="14" cy="14" r="13" fill="var(--navy)"/>
            <circle cx="14" cy="14" r="10" fill="none" stroke="#fff" stroke-width="1"/>
            <path d="M10.5 8.5c-1 .8-1.3 2.2-.6 3.8 1.2 2.7 3.1 4.6 5.8 5.8 1.6.7 3 .4 3.8-.6l-1.9-1.9-1.6 1c-1.5-.7-2.8-2-3.5-3.5l1-1.6z" fill="#fff"/>
          </svg>
          +61 (0)400 555 218
        </li>
        <li>
          <svg class="contact-icon" viewBox="0 0 28 28" aria-hidden="true">
            <circle cx="14" cy="14" r="13" fill="var(--navy)"/>
            <circle cx="14" cy="14" r="10" fill="none" stroke="#fff" stroke-width="1"/>
            <rect x="8.5" y="10" width="11" height="8" fill="#fff"/>
            <path d="M8.5 10l5.5 4.5 5.5-4.5" fill="none" stroke="var(--navy)" stroke-width="1"/>
          </svg>
          mara@pexlamedia.com.au
        </li>
        <li>
          <svg class="contact-icon" viewBox="0 0 28 28" aria-hidden="true">
            <circle cx="14" cy="14" r="13" fill="var(--navy)"/>
            <circle cx="14" cy="14" r="10" fill="none" stroke="#fff" stroke-width="1"/>
            <circle cx="14" cy="14" r="6" fill="none" stroke="#fff" stroke-width="1.2"/>
            <ellipse cx="14" cy="14" rx="2.6" ry="6" fill="none" stroke="#fff" stroke-width="1"/>
            <line x1="8" y1="14" x2="20" y2="14" stroke="#fff" stroke-width="1"/>
          </svg>
          www.pexlamedia.com.au
        </li>
      </ul>
    </div>
  </section>

  <section class="card card-back">
    <div class="back-map" role="img" aria-label="White network-style world map of connected dots"></div>
    <div class="back-brand">
      <div class="wordmark">Pexla</div>
      <span class="tm">TM</span>
    </div>
  </section>

</body>
</html>
```